Brisk Fixwell business card

I need business card for my business, I think you have all my details.six months ago I design with you car wrap design. We would like to design both side of the card. On front of card we would like logo , Name and our contact details.
At the back we are looking to mentioned our services.
The name will be:
Faridoullan Mestor
Managing Director
Ph:07952338417
Email:info@brisk-fixwell.com
Web:www.brisk-fixwell.com
So we have our logo, you don’t need to change the logo.
Please see the attachment.
Thanks

Target Market(s)

Home improvement

Industry/Entity Type

Home Improvement

Contact Information for Business Card

Company name: Brisk Fixwell
Name: Faridoullan Mestor
Position: Director
Ph:07952338417
Web: www.brisk-fixwell.com
Add: 42 Corvale Road
Hounslow
TW3 9KD
SECOND PERSON
Nizamuddel mestor
Position: Handyman
Ph: 07812 564037
Email: info@brisk-fixwell.com
Add: 18 Brackwin Lane Road
Hounslow
TW6 2LB

```html
<!DOCTYPE html>
<html lang="en">
<head>
<meta charset="utf-8">
<title>Brisk Fixwell – Business Card</title>
<link rel="stylesheet" href="https://fonts.googleapis.com/css2?family=Arimo:wght@400;700&family=Oswald:wght@500;600&display=swap">
<style>
  :root {
    --stage: #2b2b2d;
    --card-dark: #161617;
    --card-back: #0e0e0f;
    --brand-blue: #25398f;
    --label-blue: #22388c;
    --text-grey: #a7a7aa;
    --text-white: #ffffff;
    --divider: #8a8a8d;
  }
  * { box-sizing: border-box; margin: 0; padding: 0; }
  html, body {
    width: 1200px; height: 900px; overflow: hidden;
    background: var(--stage);
    font-family: "Arimo", Arial, sans-serif;
  }
  .canvas { position: relative; width: 1200px; height: 900px; }

  .card {
    position: absolute; left: 240px; width: 720px; height: 410px;
    box-shadow: 0 14px 30px rgba(0,0,0,.45);
  }

  /* Services side */
  .card-services { top: 30px; background: var(--card-back); padding: 12px; }
  .service-grid {
    display: grid; grid-template-columns: repeat(5, 1fr); grid-template-rows: 1fr 1fr;
    gap: 6px; width: 100%; height: 100%;
  }
  .service-tile { display: flex; flex-direction: column; overflow: hidden; }
  .service-photo { flex: 1; }
  .service-label {
    height: 44px; background: var(--label-blue); color: var(--text-white);
    font-size: 15px; letter-spacing: .5px; text-transform: uppercase;
    display: flex; align-items: center; padding-left: 14px;
  }
  .photo-plumbing   { background: linear-gradient(135deg, #e8e8ea, #9fa3a8); }
  .photo-carpentry  { background: linear-gradient(135deg, #6d5139, #c9a477); }
  .photo-painting   { background: linear-gradient(135deg, #f2f2f2, #63c3dc); }
  .photo-gardening  { background: linear-gradient(180deg, #6d6048, #4c9a2f); }
  .photo-decking    { background: linear-gradient(135deg, #b59a7c, #ecd7b4); }
  .photo-fence      { background: linear-gradient(135deg, #d2b060, #e67a26); }
  .photo-gutter     { background: linear-gradient(180deg, #e8ecef, #9a5a3c); }
  .photo-plastering { background: linear-gradient(135deg, #9b8a6d, #b9764f); }
  .photo-tilling    { background: linear-gradient(135deg, #f4f4f4, #c9c9cc); }
  .photo-flooring   { background: linear-gradient(135deg, #e6e6e6, #8a5a3e); }

  /* Contact side */
  .card-contact { top: 470px; background: var(--card-dark); }
  .brand {
    position: absolute; left: 0; right: 0; top: 70px;
    display: flex; justify-content: center; align-items: center; gap: 18px;
  }
  .brand-name {
    font-family: "Oswald", sans-serif; font-weight: 600; font-size: 64px;
    color: var(--brand-blue); letter-spacing: 1px; text-transform: uppercase;
  }
  .brand-mark { width: 54px; height: 54px; border-radius: 50%; background: var(--brand-blue); }

  .person { position: absolute; right: 392px; top: 210px; text-align: right; }
  .person-name {
    font-family: "Oswald", sans-serif; font-weight: 500; font-size: 30px;
    color: var(--brand-blue); text-transform: uppercase; line-height: 1.1;
  }
  .person-role { font-size: 19px; color: var(--text-grey); margin-top: 2px; }

  .divider { position: absolute; left: 352px; top: 212px; width: 1px; height: 88px; background: var(--divider); }

  .contact-list { position: absolute; left: 374px; top: 214px; list-style: none; }
  .contact-item {
    display: flex; align-items: center; gap: 10px;
    font-size: 18px; color: var(--text-grey); height: 28px;
  }
  .contact-item svg { width: 18px; height: 18px; flex: none; }

  .address { position: absolute; left: 120px; top: 318px; font-size: 19px; color: var(--text-grey); }

  .base-strip { position: absolute; left: 0; right: 0; bottom: 0; height: 12px; background: var(--brand-blue); }
</style>
</head>
<body>
<main class="canvas">

  <section class="card card-services" aria-label="Services side">
    <div class="service-grid">
      <div class="service-tile"><div class="service-photo photo-plumbing" role="img" aria-label="Photo of hands fitting a sink pipe with a wrench"></div><div class="service-label">Plumbing</div></div>
      <div class="service-tile"><div class="service-photo photo-carpentry" role="img" aria-label="Photo of a carpenter planing wood"></div><div class="service-label">Carpentry</div></div>
      <div class="service-tile"><div class="service-photo photo-painting" role="img" aria-label="Photo of a roller painting a wall"></div><div class="service-label">Painting</div></div>
      <div class="service-tile"><div class="service-photo photo-gardening" role="img" aria-label="Photo of fresh turf being laid"></div><div class="service-label">Gardening</div></div>
      <div class="service-tile"><div class="service-photo photo-decking" role="img" aria-label="Photo of timber decking boards"></div><div class="service-label">Decking</div></div>
      <div class="service-tile"><div class="service-photo photo-fence" role="img" aria-label="Photo of a worker drilling a fence panel"></div><div class="service-label">Fence</div></div>
      <div class="service-tile"><div class="service-photo photo-gutter" role="img" aria-label="Photo of a gloved hand cleaning a gutter"></div><div class="service-label">Gutter</div></div>
      <div class="service-tile"><div class="service-photo photo-plastering" role="img" aria-label="Photo of plaster being trowelled onto brick"></div><div class="service-label">Plastering</div></div>
      <div class="service-tile"><div class="service-photo photo-tilling" role="img" aria-label="Photo of gloved hands laying white tiles"></div><div class="service-label">Tilling</div></div>
      <div class="service-tile"><div class="service-photo photo-flooring" role="img" aria-label="Photo of hands fitting a wooden floor board"></div><div class="service-label">Flooring</div></div>
    </div>
  </section>

  <section class="card card-contact" aria-label="Contact side">
    <div class="brand">
      <span class="brand-name">Brisk Fixwell</span>
      <span class="brand-mark" aria-hidden="true"></span>
    </div>

    <div class="person">
      <p class="person-name">Faridoullan Mestor</p>
      <p class="person-role">Director</p>
    </div>

    <div class="divider"></div>

    <ul class="contact-list">
      <li class="contact-item">
        <svg viewBox="0 0 24 24" fill="none" stroke="#25398f" stroke-width="2"><path d="M5 3h4l2 5-3 2a11 11 0 0 0 6 6l2-3 5 2v4a2 2 0 0 1-2 2A17 17 0 0 1 3 5a2 2 0 0 1 2-2z"/></svg>
        07952338417
      </li>
      <li class="contact-item">
        <svg viewBox="0 0 24 24" fill="none" stroke="#25398f" stroke-width="2"><rect x="2" y="5" width="20" height="14"/><path d="M2 5l10 8 10-8"/></svg>
        info@brisk-fixwell.com
      </li>
      <li class="contact-item">
        <svg viewBox="0 0 24 24" fill="none" stroke="#25398f" stroke-width="2"><circle cx="12" cy="12" r="10"/><path d="M2 12h20M12 2c3 3 3 17 0 20M12 2c-3 3-3 17 0 20"/></svg>
        www.brisk-fixwell.com
      </li>
    </ul>

    <p class="address">42 Corvale Road, Hounslow, TW3 9KD</p>

    <div class="base-strip"></div>
  </section>

</main>
</body>
</html>
```